Creative, fresh business card design for Ripplecraft Facades

We need a fresh, creative business card design for Ripplecraft Facades. We are the manufacturer of Ripplecraft Facades in Australia. Wall panels are 2400 x 1200mm panels made from MDF and feature 3D patterns on the face of the panel. The colours to be used are green, silver/grey and white RGB
Red 187
Green 207
Blue 65.

An idea is to possibly use a watermark of one of our designs as a background (like on the "Grids" design on the left hand side of page 2 of our brochure).

Target Market(s)

Interior designers, architects, builders and home renovators

Industry/Entity Type

Business

Contact Information for Business Card

Details to go on the card are:
Our logo (attached),
Slogan: "Decorative panels for interiors and exteriors",
Contact name,
Position,
Mobile phone number,
Business address,
Business phone,
Business fax,
Website and
Email address.

I have attached a few images of our panels and our brochure for reference.

The colours of the business card should feature our logo colours which are: RGB
Red 187
Green 207
Blue 65

Requirements
Must have
• Very modern fonts and design. Some of the designs shown especially the "Prisms" design which is a popular design.
Nice to have
• Creative but simple design. Very contemporary.
Should not have
• Anything ornate or old fashioned.

```html
<!DOCTYPE html>
<html lang="en">
<head>
<meta charset="utf-8">
<title>Ripplecraft Facades – Business Card</title>
<link href="https://fonts.googleapis.com/css2?family=Questrial&display=swap" rel="stylesheet">
<style>
  :root {
    --page: #e9e6e1;
    --card: #141414;
    --card-edge: #0a0a0a;
    --ripple-a: #1c1c1c;
    --ripple-b: #0e0e0e;
    --green: #bbcf41;
    --silver: #b9b9b9;
    --text-light: #d4d4d4;
    --text-muted: #8c8c8c;
    --ink: #141414;
  }
  * { box-sizing: border-box; margin: 0; padding: 0; }
  html, body {
    width: 1200px; height: 1022px; overflow: hidden;
    background: var(--page);
    font-family: "Questrial", "Century Gothic", sans-serif;
  }
  .sheet {
    position: relative; width: 1200px; height: 1022px;
  }
  .card {
    position: absolute; left: 250px; width: 700px; height: 400px;
    background: var(--card);
    border: 1px solid var(--card-edge);
    box-shadow: 0 14px 30px rgba(0,0,0,.25);
    overflow: hidden;
  }
  .card--front { top: 81px; }
  .card--back { top: 541px; }

  .ripple-texture {
    position: absolute; inset: 0;
    background: radial-gradient(circle at 40% 45%, var(--ripple-a) 0%, var(--ripple-b) 75%);
  }

  /* Front */
  .person {
    position: absolute; left: 64px; bottom: 70px;
  }
  .person__rule {
    position: absolute; left: 210px; top: -6px;
    width: 320px; height: 4px; background: var(--green);
  }
  .person__name {
    color: var(--green); font-size: 34px; letter-spacing: 1px; line-height: 1.1;
  }
  .person__role {
    color: var(--text-muted); font-size: 20px; letter-spacing: 1px; margin-top: 4px;
  }

  /* Back */
  .brand {
    position: absolute; left: 56px; top: 52px;
    display: flex; align-items: flex-end;
  }
  .brand__square {
    width: 116px; height: 116px; background: var(--green);
  }
  .brand__band {
    background: var(--silver); color: var(--ink);
    font-size: 24px; padding: 6px 16px; letter-spacing: .5px;
    line-height: 1.2;
  }
  .slogan {
    position: absolute; left: 56px; top: 186px;
    color: var(--text-muted); font-size: 17px; letter-spacing: 2px; line-height: 1.35;
  }
  .address {
    position: absolute; left: 56px; top: 262px;
    color: var(--text-light); font-size: 19px; letter-spacing: 1.5px; line-height: 1.45;
  }
  .contacts {
    position: absolute; right: 56px; top: 186px;
    list-style: none;
  }
  .contacts__item {
    display: flex; align-items: center; gap: 14px;
    color: var(--text-light); font-size: 19px; letter-spacing: 1.5px;
    height: 34px;
  }
  .contacts__icon { width: 18px; height: 18px; flex: none; }
</style>
</head>
<body>
<main class="sheet">

  <section class="card card--front" aria-label="Card front">
    <div class="ripple-texture" role="img" aria-label="Faint embossed ripple panel pattern"></div>
    <div class="person">
      <span class="person__rule"></span>
      <p class="person__name">Liam Draper</p>
      <p class="person__role">President</p>
    </div>
  </section>

  <section class="card card--back" aria-label="Card back">
    <div class="ripple-texture" role="img" aria-label="Faint embossed ripple panel pattern"></div>

    <div class="brand">
      <span class="brand__square"></span>
      <span class="brand__band">Ripplecraft Facades</span>
    </div>

    <p class="slogan">decorative panels for<br>interiors &amp; landscapes</p>

    <p class="address">412 Harbour Lane<br>Westbrook, VIC 3171</p>

    <ul class="contacts">
      <li class="contacts__item">
        <svg class="contacts__icon" viewBox="0 0 18 18"><rect x="5" y="1" width="8" height="16" rx="1.5" fill="none" stroke="var(--green)" stroke-width="1.8"/><circle cx="9" cy="14" r="1" fill="var(--green)"/></svg>
        041. 736. 5920
      </li>
      <li class="contacts__item">
        <svg class="contacts__icon" viewBox="0 0 18 18"><path d="M4 2 L7 2 L8 6 L6 7.5 C7 10 8 11 10.5 12 L12 10 L16 11 L16 14 C16 15 15 16 14 16 C8 16 2 10 2 4 C2 3 3 2 4 2 Z" fill="var(--green)"/></svg>
        039. 418. 6621
      </li>
      <li class="contacts__item">
        <svg class="contacts__icon" viewBox="0 0 18 18"><rect x="5" y="1" width="8" height="5" fill="var(--green)"/><rect x="1" y="7" width="16" height="7" rx="1" fill="var(--green)"/><rect x="5" y="12" width="8" height="5" fill="var(--green)" stroke="var(--card)" stroke-width="1"/></svg>
        039. 418. 6622
      </li>
      <li class="contacts__item">
        <svg class="contacts__icon" viewBox="0 0 18 18"><rect x="1" y="4" width="16" height="11" fill="var(--green)"/><path d="M1 4 L9 10 L17 4" fill="none" stroke="var(--card)" stroke-width="1.4"/></svg>
        liam@ripplecraft.net
      </li>
      <li class="contacts__item">
        <svg class="contacts__icon" viewBox="0 0 18 18"><circle cx="9" cy="9" r="7.5" fill="none" stroke="var(--green)" stroke-width="1.8"/><ellipse cx="9" cy="9" rx="3.2" ry="7.5" fill="none" stroke="var(--green)" stroke-width="1.4"/><line x1="1.5" y1="9" x2="16.5" y2="9" stroke="var(--green)" stroke-width="1.4"/></svg>
        www.ripplecraft.net
      </li>
    </ul>
  </section>

</main>
</body>
</html>
```